Business card for marketing analytics company

Need a business card for new company. I have a logo already that I want to be built into the card and should use those colours

Company is called steered by tallies
Design must bring steered by tallies to life not be a card that could be for anyone with a logo put on it.

Like the front to be fairly clean and uncluttered bringing the logo out with a suitable design on the back of the card.

The logo represents a compass and business growth so those themes along with numbers, analytics , data are appropriate.
I'm often working with creative industries so also needs to reflect the creative side of analytics rather than be very corporate looking.

Target Market(s)

Ad agency, media agency, consumer goods clients

Industry/Entity Type

Market Research

Contact Information for Business Card

Needs to include name, title, email and phone number

Colors
f78f20
f68d4d
ec1f27

Requirements
Must have
• Must bring steered by tallies to life not be a card that could be for anyone with a logo put on it.
• Logo, Correct colours
• Like a design on the back that relates to company name
• Designs for both sides
Should not have
• Please do not just submit logo and a coloured card.
• It needs to have a design element to it
• No black background
• No clear cards - needs front & back

```html
<!DOCTYPE html>
<html lang="en">
<head>
<meta charset="utf-8">
<title>Steered by Tallies – Business Card</title>
<link rel="stylesheet" href="https://fonts.googleapis.com/css2?family=Open+Sans:wght@400;600&display=swap">
<style>
  :root {
    --backdrop: #6b6b6e;
    --card-white: #f4f4f2;
    --brand-red: #ec1f27;
    --brand-orange: #f78f20;
    --brand-coral: #f68d4d;
    --ink-grey: #55585c;
    --paper-white: #ffffff;
  }
  html, body {
    margin: 0;
    padding: 0;
    width: 1200px;
    height: 913px;
    overflow: hidden;
    background: var(--backdrop);
    font-family: "Open Sans", Arial, sans-serif;
  }
  .canvas {
    width: 1200px;
    height: 913px;
    display: flex;
    align-items: center;
    justify-content: center;
    gap: 60px;
  }
  .card {
    position: relative;
    width: 520px;
    height: 297px;
    border-radius: 3px;
    overflow: hidden;
    box-shadow: 0 6px 18px rgba(0,0,0,0.25);
  }
  /* Back of card */
  .card-back {
    background: var(--brand-orange);
  }
  .card-back .colour-split {
    position: absolute;
    inset: 0;
    width: 100%;
    height: 100%;
  }
  .holder {
    position: absolute;
    top: 22px;
    right: 28px;
    text-align: left;
  }
  .holder-name {
    margin: 0;
    font-weight: 600;
    font-size: 20px;
    letter-spacing: 0.5px;
    color: var(--brand-orange);
  }
  .holder-title {
    margin: 2px 0 0;
    font-weight: 400;
    font-size: 15px;
    color: var(--paper-white);
  }
  .feature-mark {
    position: absolute;
    left: 34px;
    top: 98px;
    display: flex;
    align-items: center;
    gap: 18px;
  }
  .feature-ring {
    width: 76px;
    height: 76px;
    box-sizing: border-box;
    border-radius: 50%;
    border: 5px solid var(--paper-white);
  }
  .feature-name {
    margin: 0;
    font-weight: 600;
    font-size: 30px;
    color: var(--paper-white);
  }
  .contact-list {
    position: absolute;
    left: 30px;
    bottom: 24px;
    margin: 0;
    padding: 0;
    list-style: none;
    font-size: 13px;
    line-height: 1.45;
    color: var(--paper-white);
  }
  /* Front of card */
  .card-front {
    background: var(--card-white);
    display: flex;
    align-items: center;
    justify-content: center;
  }
  .wordmark {
    display: flex;
    align-items: center;
    gap: 18px;
  }
  .wordmark-dot {
    width: 46px;
    height: 46px;
    border-radius: 50%;
    background: var(--brand-orange);
  }
  .wordmark-name {
    margin: 0;
    font-weight: 400;
    font-size: 34px;
    color: var(--ink-grey);
  }
</style>
</head>
<body>
<main class="canvas">
  <section class="card card-back" aria-label="Card back with contact details">
    <svg class="colour-split" viewBox="0 0 520 297" preserveAspectRatio="none" aria-hidden="true">
      <polygon points="0,0 520,0 520,120 0,215" fill="var(--brand-red)"/>
    </svg>
    <div class="holder">
      <p class="holder-name">MARTIN HALE</p>
      <p class="holder-title">CEO/Founder</p>
    </div>
    <div class="feature-mark">
      <span class="feature-ring" aria-hidden="true"></span>
      <p class="feature-name">Steered by Tallies</p>
    </div>
    <ul class="contact-list">
      <li>Phone : 555 210 4873</li>
      <li>martin@steeredbytallies.com</li>
      <li>www.steeredbytallies.com</li>
    </ul>
  </section>

  <section class="card card-front" aria-label="Card front with company name">
    <div class="wordmark">
      <span class="wordmark-dot" aria-hidden="true"></span>
      <p class="wordmark-name">Steered by Tallies</p>
    </div>
  </section>
</main>
</body>
</html>
```